A private security company called "Tavron Security Services Ltd"

Hello everybody,

We need a web page for a company based in NZ. It is mainly an informative website so it would be wonderful if the designer puts their absolute best into making it a website that I would really appreciate. The website needs to show professionalism and also needs to make our web surfers find the information they need in a click. the company's colour is black and silver, and if those two colours could be integrated into the website it would be absolutely lovely. Please do contact me for any information.

Sincerely,
Dorian Vaskel

Industry/Entity Type

Security

```html
<!DOCTYPE html>
<html lang="en">
<head>
<meta charset="utf-8">
<title>Tavron Security Services Ltd</title>
<link href="https://fonts.googleapis.com/css2?family=Oswald:wght@300;400&family=Arimo:wght@400;700&display=swap" rel="stylesheet">
<style>
:root{
  --ink:#1d1d1d;
  --text:#555;
  --muted:#8a8a8a;
  --silver:#e9e9ea;
  --silver-dark:#cfcfd1;
  --line:#d2d2d4;
  --dark:#2b2b2c;
  --darker:#1f1f20;
  --white:#fff;
  --btn:#f2f2f2;
}
*{box-sizing:border-box;margin:0;padding:0}
html,body{width:1200px;height:2757px;overflow:hidden}
body{position:relative;background:var(--white);font-family:"Arimo",Arial,sans-serif;color:var(--text)}
.abs{position:absolute}
.heading{font-family:"Oswald","Arial Narrow",sans-serif;font-weight:400;color:var(--ink)}
/* header */
.site-header{left:0;top:0;width:1200px;height:160px;background:linear-gradient(#fbfbfb,#e6e6e7)}
.brand{left:160px;top:40px;display:flex;align-items:center;gap:14px}
.brand-dot{width:46px;height:46px;border-radius:50%;background:#3a3a3a}
.brand-name{font-family:"Oswald",sans-serif;font-weight:400;color:#222;font-size:30px;line-height:30px;letter-spacing:2px;text-transform:uppercase}
.brand-name small{display:block;font-size:14px;line-height:18px;letter-spacing:.5px;text-transform:none}
.main-nav{right:140px;top:100px;display:flex;gap:34px;font-size:13px;color:#333;letter-spacing:.3px}
.social{display:flex;gap:10px}
.social span{width:30px;height:30px;border-radius:50%;background:#b8b8ba;display:block}
.header-social{left:934px;top:32px}
/* hero */
.hero{left:0;top:160px;width:1200px;height:516px;background:radial-gradient(ellipse at 45% 40%,#555 0%,#3b3b3c 45%,#232324 100%)}
.hero-title{left:216px;top:222px;font-family:"Oswald",sans-serif;font-weight:300;color:#f2f2f2;font-size:31px;line-height:46px}
.hero-title b{font-weight:400;font-size:38px}
.arrow{width:50px;height:50px;border-radius:50%;background:rgba(120,120,120,.7)}
.hero-photo{left:690px;top:50px;width:290px;height:466px;background:linear-gradient(90deg,#6f7072,#d8d8da 50%,#8a8b8d);border-radius:4px 4px 0 0}
/* solutions */
.solutions{left:0;top:676px;width:1200px;height:710px;background:linear-gradient(90deg,#dcdcdd,#f1f1f2 50%,#dcdcdd)}
.section-title{width:1200px;text-align:center;font-size:38px}
.svc-title{left:156px;top:150px;font-size:23px}
.svc-list{left:160px;top:208px;list-style:none;font-size:13px;color:#666;width:200px}
.svc-list li{position:relative;padding-left:26px;margin-bottom:21px;line-height:17px}
.svc-list li::before{content:"";position:absolute;left:0;top:1px;width:14px;height:14px;border-radius:50%;background:#d0d0d2}
.svc-list li::after{content:"";position:absolute;left:4px;top:5px;width:4px;height:4px;border-right:1.5px solid #777;border-top:1.5px solid #777;transform:rotate(45deg)}
.custom-box{left:158px;top:420px;width:210px;height:254px;background:linear-gradient(#8c8c8e,#d7d7d9 60%,#b5b5b7);padding:22px 16px}
.custom-box p{font-family:"Oswald",sans-serif;color:#fff;font-size:19px;line-height:24px;text-transform:uppercase}
.custom-box p.call{font-size:24px;line-height:32px}
.custom-box .box-name{position:absolute;left:16px;bottom:20px;font-family:"Oswald",sans-serif;color:#222;font-size:18px;line-height:20px;text-transform:uppercase;letter-spacing:1px}
.grid{left:370px;top:150px;width:676px;height:560px;border-left:1px solid var(--line)}
.col{position:absolute;top:0;width:225px;height:560px;border-right:1px solid var(--line)}
.card{position:absolute;left:0;width:224px;padding:10px 14px 0 14px}
.card h3{font-family:"Oswald",sans-serif;font-weight:400;color:var(--ink);font-size:18px;margin-bottom:14px}
.card p{font-size:11px;line-height:15px;color:#777}
.card .btn{margin:14px 0 0 auto;display:block}
.split{position:absolute;left:0;width:224px;border-top:1px solid #fff;box-shadow:0 -1px 0 var(--line)}
.btn{width:70px;height:28px;border:1px solid #bdbdbf;background:linear-gradient(#fff,#e2e2e3);font-size:11px;color:#333;text-align:center;line-height:26px;border-radius:2px}
/* industries */
.industries{left:0;top:1386px;width:1200px;height:404px;background:var(--white)}
.ind-card{top:144px;width:194px;text-align:center}
.ind-photo{width:194px;height:158px;border:5px solid #e6e6e7;box-shadow:0 1px 3px rgba(0,0,0,.25)}
.ind-card h4{margin-top:14px;font-family:"Oswald",sans-serif;font-weight:400;font-size:18px;color:var(--ink)}
.small-arrow{width:34px;height:34px;border-radius:50%;background:#c6c6c8}
/* offers */
.offers{left:0;top:1790px;width:1200px;height:480px;background:linear-gradient(#ededee,#f7f7f8)}
.offer{top:64px;width:260px;text-align:center}
.ring{margin:0 auto;width:184px;height:184px;border-radius:50%;background:#fff;box-shadow:0 1px 5px rgba(0,0,0,.2);padding:9px}
.ring div{width:166px;height:166px;border-radius:50%}
.offer h4{margin-top:18px;font-family:"Oswald",sans-serif;font-weight:400;font-size:18px;color:var(--ink)}
.offer p{margin:8px auto 0;width:240px;font-size:12px;line-height:15px;color:#999}
.offer .btn{margin:20px auto 0;width:112px;height:30px;line-height:28px;font-size:12px}
/* footer */
.site-footer{left:0;top:2270px;width:1200px;height:487px;background:radial-gradient(ellipse at 50% 0%,#4a4a4b,var(--dark) 45%,var(--darker))}
.foot-title{top:60px;font-family:"Oswald",sans-serif;font-weight:300;font-size:27px;color:#f3f3f3}
.about-text{left:158px;top:128px;width:304px;font-size:11px;line-height:15px;color:#8a8a8b}
.about-text p{margin-bottom:14px}
.quick{left:540px;top:124px;list-style:none;font-size:12px;color:#9a9a9b}
.quick li{padding-left:20px;position:relative;margin-bottom:17px;text-transform:uppercase}
.quick li::before{content:"";position:absolute;left:0;top:3px;width:5px;height:5px;border-right:2px solid #ddd;border-top:2px solid #ddd;transform:rotate(45deg)}
.news-note{left:766px;top:126px;width:280px;font-size:11px;line-height:15px;color:#8a8a8b}
.field{left:766px;width:276px;height:36px;background:#5a5a5b;border:1px solid #6a6a6b;font-size:12px;color:#ccc;line-height:34px;padding-left:18px}
.signup{left:766px;top:290px;width:146px;height:36px;background:linear-gradient(#fff,#dcdcdd);font-size:12px;color:#333;text-align:center;line-height:36px;border-radius:2px}
.foot-rule{left:158px;top:388px;width:884px;border-top:1px solid #3c3c3d}
.copyright{left:158px;top:421px;font-size:11px;color:#8a8a8b}
.footer-social{left:934px;top:414px}
.footer-social span{background:#7a7a7b}
</style>
</head>
<body>

<header class="site-header abs">
  <div class="brand abs"><span class="brand-dot"></span><div class="brand-name">Tavron<small>Security Services Ltd.</small></div></div>
  <nav class="main-nav abs"><span>HOME</span><span>OUR SERVICES</span><span>ABOUT</span><span>LOCATIONS</span><span>NEWS</span><span>CAREERS</span><span>CONTACT US</span></nav>
  <div class="social header-social abs" aria-label="Social links"><span></span><span></span><span></span></div>
</header>

<section class="hero abs">
  <div class="arrow abs" style="left:103px;top:231px"><svg width="50" height="50"><polyline points="29,16 20,25 29,34" fill="none" stroke="#fff" stroke-width="2"/></svg></div>
  <div class="arrow abs" style="left:1045px;top:231px"><svg width="50" height="50"><polyline points="21,16 30,25 21,34" fill="none" stroke="#fff" stroke-width="2"/></svg></div>
  <h1 class="hero-title abs"><b>Lorem Ipsum</b> is simply dummy text of<br>the printing and typesetting industry.</h1>
  <div class="hero-photo abs" role="img" aria-label="Security camera mounted on a pole"></div>
</section>

<section class="solutions abs">
  <h2 class="section-title heading abs" style="top:50px">Our Security Solutions</h2>
  <h3 class="svc-title heading abs">Services</h3>
  <ul class="svc-list abs">
    <li>Property guards</li>
    <li>Corporate events security</li>
    <li>Personal bodyguard for high net worth individuals</li>
    <li>Security consultancy</li>
    <li>Private investigation</li>
  </ul>
  <div class="custom-box abs">
    <p>Custom options<br>available</p>
    <p class="call">Call 021-555-0147</p>
    <div class="box-name">Tavron<br>Security Services Ltd.</div>
  </div>
  <div class="grid abs">
    <div class="col" style="left:0">
      <article class="card" style="top:0"><h3>Property Guards</h3><p>Trained guards patrol your site day and night, check each entry point and log every event.</p><p style="margin-top:14px">Our staff keep people safe and assets secure while your team gets on with its work.</p><div class="btn">Read More</div></article>
      <div class="split" style="top:246px"></div>
      <article class="card" style="top:262px"><h3>Corporate Events Security</h3><p>We plan access, crowd flow and guest checks for launches, dinners and large company events, so every guest feels welcome and every door stays under watch from the first arrival to the last departure.</p><div class="btn">Read More</div></article>
    </div>
    <div class="col" style="left:225px">
      <article class="card" style="top:0"><h3>Personal Bodyguards</h3><p>Discreet close protection for leaders, public figures and families who need a calm, trusted presence.</p><p style="margin-top:14px">Each officer is vetted, trained in first aid and skilled in route planning and safe travel.</p><div class="btn">Read More</div></article>
      <div class="split" style="top:270px"></div>
      <article class="card" style="top:286px"><h3>Security Consultancy</h3><p>Our advisers review your sites, staff and systems, then deliver a clear plan with costs and priorities that lowers risk and fits the way your business really runs each day.</p><div class="btn">Read More</div></article>
    </div>
    <div class="col" style="left:450px">
      <article class="card" style="top:0"><h3>Private Investigation</h3><p>Licensed investigators handle fraud checks, background reviews and asset tracing with care and full discretion.</p><div class="btn">Read More</div></article>
      <div class="split" style="top:232px"></div>
      <article class="card" style="top:248px"><h3>Executive Protection</h3><p>Protection teams for senior staff on the road or at home, with threat reviews, secure transport and a single contact point for every trip and every meeting you need.</p><div class="btn">Read More</div></article>
    </div>
  </div>
</section>

<section class="industries abs">
  <h2 class="section-title heading abs" style="top:50px">Industries We Serve</h2>
  <div class="small-arrow abs" style="left:107px;top:205px"><svg width="34" height="34"><polyline points="20,11 14,17 20,23" fill="none" stroke="#fff" stroke-width="2"/></svg></div>
  <div class="small-arrow abs" style="left:1057px;top:205px"><svg width="34" height="34"><polyline points="14,11 20,17 14,23" fill="none" stroke="#fff" stroke-width="2"/></svg></div>
  <div class="ind-card abs" style="left:158px"><div class="ind-photo" role="img" aria-label="Officer on a college campus" style="background:linear-gradient(#8fa06d,#5e6b48)"></div><h4>Campus Security</h4></div>
  <div class="ind-card abs" style="left:388px"><div class="ind-photo" role="img" aria-label="Guard patrolling a shopping mall" style="background:linear-gradient(#b59a74,#5a4a3a)"></div><h4>Shoping Center</h4></div>
  <div class="ind-card abs" style="left:618px"><div class="ind-photo" role="img" aria-label="Cameras watching an industrial site" style="background:linear-gradient(#d7e2ea,#8fa3b3)"></div><h4>Industrial Security</h4></div>
  <div class="ind-card abs" style="left:848px"><div class="ind-photo" role="img" aria-label="Operator at a monitoring desk" style="background:linear-gradient(#5b6a78,#2a2f36)"></div><h4>Security Monitoring</h4></div>
</section>

<section class="offers abs">
  <div class="offer abs" style="left:144px"><div class="ring"><div role="img" aria-label="Resident using a home alarm keypad" style="background:linear-gradient(#d9c9b4,#8e7a66)"></div></div><h4>Residential Solutions</h4><p>Alarm, patrol and response plans for homes of every size, with fast help on call.</p><div class="btn">Read More</div></div>
  <div class="offer abs" style="left:470px"><div class="ring"><div role="img" aria-label="Guard outside an office building" style="background:linear-gradient(#9bb3cf,#3b4656)"></div></div><h4>Commercial Solutions</h4><p>Guarding, access control and key holding for offices, shops and large sites nationwide.</p><div class="btn">Read More</div></div>
  <div class="offer abs" style="left:796px"><div class="ring"><div role="img" aria-label="Control room with monitoring screens" style="background:linear-gradient(#6f9ab8,#2c3e50)"></div></div><h4>Technology Solutions</h4><p>Cameras, alarms and remote monitoring designed, fitted and serviced by our own team.</p><div class="btn">Read More</div></div>
</section>

<footer class="site-footer abs">
  <h3 class="foot-title abs" style="left:158px">About us</h3>
  <div class="about-text abs">
    <p>Tavron is a New Zealand owned security firm serving homes, firms and events. We focus on trained people, clear reports and quick response across the country every day.</p>
    <p>Since our start we have grown a team of licensed guards, advisers and technicians. We work closely with each client to build a plan that suits their site, budget and goals, and we review it often so it keeps pace with change.</p>
  </div>
  <h3 class="foot-title abs" style="left:540px">Quick Links</h3>
  <ul class="quick abs"><li>Home</li><li>Our Services</li><li>About</li><li>Locations</li><li>News</li><li>Careers</li><li>Contact Us</li></ul>
  <h3 class="foot-title abs" style="left:766px">Newsletter Sigup</h3>
  <p class="news-note abs">Fill the form below and recive our latest offers &amp; updates</p>
  <div class="field abs" style="top:190px">Your Name</div>
  <div class="field abs" style="top:236px">Your Email</div>
  <div class="signup abs">Signup Now!</div>
  <div class="foot-rule abs"></div>
  <p class="copyright abs">Copyright © 2014 Tavron Security Service LTD.</p>
  <div class="social footer-social abs" aria-label="Social links"><span></span><span></span><span></span></div>
</footer>

</body>
</html>
```